Tolbek cards

I want a simple business card that pops.
Logo on one side.
On side two i want.
"Are you thinking about a new building on your property, or renovating an existing structure? Contact".....
Owners Name: Dale Whitacre
Owners Phone number: 610-555-0187
Address:4076 Copper Ridge RD, Alder Glen, PA 16940
Committed to Quality, Service, and Integrity

```html
<!DOCTYPE html>
<html lang="en">
<head>
<meta charset="utf-8">
<title>Tolbek Builders business card</title>
<link rel="stylesheet" href="https://fonts.googleapis.com/css2?family=Archivo:wght@400;500;700;800&display=swap">
<style>
  :root {
    --backdrop: #2a2a2a;
    --bronze-light: #9c8468;
    --bronze-dark: #583d2a;
    --espresso: #573a27;
    --tan: #a08565;
    --paper: #f4f3f1;
    --ink: #4a3323;
    --ink-soft: #5a4636;
    --cream: #f1ece6;
  }
  * { margin: 0; padding: 0; box-sizing: border-box; }
  html, body { width: 1200px; height: 576px; overflow: hidden; }
  body {
    background: var(--backdrop);
    font-family: "Archivo", Arial, sans-serif;
    position: relative;
  }
  .card {
    position: absolute;
    top: 139px;
    width: 484px;
    height: 292px;
    border-radius: 10px;
    overflow: hidden;
  }
  .card-front {
    left: 102px;
    background: linear-gradient(180deg, var(--bronze-light) 0%, #7d6248 55%, var(--bronze-dark) 100%);
  }
  .card-back {
    left: 596px;
    background: var(--paper);
  }

  /* Front */
  .front-name {
    position: absolute;
    left: 0; right: 0;
    top: 92px;
    text-align: center;
    color: var(--cream);
    font-weight: 800;
    line-height: 1;
  }
  .front-name .word { display: block; font-size: 50px; letter-spacing: 1px; text-transform: uppercase; }
  .front-name .suffix { display: block; font-size: 17px; letter-spacing: 2px; margin-top: 8px; text-transform: uppercase; }
  .front-tagline {
    position: absolute;
    left: 0; right: 0;
    top: 255px;
    display: flex;
    align-items: center;
    justify-content: center;
    gap: 10px;
    color: var(--cream);
    font-size: 12.5px;
  }
  .front-tagline .rule { width: 72px; height: 1px; background: rgba(241,236,230,0.7); }

  /* Back */
  .contact-label {
    position: absolute;
    left: 28px; top: 45px;
    display: flex; align-items: center; gap: 4px;
    font-size: 8.5px; color: var(--ink-soft);
  }
  .contact-label .rule { width: 170px; height: 1px; background: #b9aea3; }
  .owner-name {
    position: absolute;
    left: 28px; top: 59px;
    font-size: 19px; font-weight: 700; letter-spacing: 0.3px;
    color: var(--ink); text-transform: uppercase;
  }
  .owner-name .last { color: var(--tan); }
  .contact-list {
    position: absolute;
    left: 28px; top: 84px;
    list-style: none;
    font-size: 12px; color: var(--ink); line-height: 16px;
  }
  .contact-list li { display: flex; gap: 6px; margin-bottom: 4px; }
  .contact-list svg { flex: none; margin-top: 2px; }
  .back-tagline {
    position: absolute;
    left: 28px; top: 165px;
    font-size: 11.5px; line-height: 15px; color: var(--ink);
  }
  .back-name {
    position: absolute;
    left: 280px; width: 180px; top: 82px;
    text-align: center;
    color: var(--ink); font-weight: 800; line-height: 1;
  }
  .back-name .word { display: block; font-size: 34px; text-transform: uppercase; }
  .back-name .suffix { display: block; font-size: 12px; letter-spacing: 1.5px; margin-top: 6px; text-transform: uppercase; }
  .wave { position: absolute; left: 0; top: 0; }
  .pitch {
    position: absolute;
    right: 28px; top: 198px;
    text-align: right;
    font-size: 12.5px; line-height: 19px; color: var(--cream);
  }
</style>
</head>
<body>
  <section class="card card-front" aria-label="Card front">
    <div class="front-name">
      <span class="word">Tolbek</span>
      <span class="suffix">Builders LLC</span>
    </div>
    <div class="front-tagline">
      <span class="rule"></span>
      <span>Committed to Quality, Service &amp; Integrity</span>
      <span class="rule"></span>
    </div>
  </section>

  <section class="card card-back" aria-label="Card back">
    <svg class="wave" width="484" height="292" viewBox="0 0 484 292" aria-hidden="true">
      <path d="M0,258 C90,300 210,262 300,222 C380,188 440,190 484,198 L484,292 L0,292 Z" fill="var(--espresso)"/>
      <path d="M0,232 C80,262 170,250 250,224 C330,196 420,158 484,166 L484,176 C420,170 340,204 260,232 C180,258 90,270 0,244 Z" fill="var(--tan)"/>
      <path d="M38,232 C120,258 220,236 300,206 C230,240 140,262 38,232 Z" fill="var(--tan)" opacity="0.8"/>
    </svg>

    <div class="contact-label"><span>Contact:</span><span class="rule"></span></div>
    <h1 class="owner-name">Dale <span class="last">Whitacre</span></h1>
    <ul class="contact-list">
      <li>
        <svg width="11" height="11" viewBox="0 0 12 12" aria-hidden="true"><circle cx="6" cy="6" r="5.3" fill="none" stroke="var(--ink)" stroke-width="1"/><path d="M4,3.4 L5,3.2 L5.6,4.6 L5,5.1 C5.3,5.9 6,6.7 6.9,7 L7.4,6.4 L8.7,7 L8.5,8 C6,8.4 3.6,6 4,3.4 Z" fill="var(--ink)"/></svg>
        <span>610-555-0187</span>
      </li>
      <li>
        <svg width="11" height="13" viewBox="0 0 12 14" aria-hidden="true"><path d="M6,13 C6,13 1.2,8 1.2,5.2 A4.8,4.8 0 0 1 10.8,5.2 C10.8,8 6,13 6,13 Z" fill="none" stroke="var(--ink)" stroke-width="1.1"/><circle cx="6" cy="5.2" r="1.7" fill="var(--ink)"/></svg>
        <span>4076 Copper Ridge RD,<br>Alder Glen, PA 16940</span>
      </li>
    </ul>
    <p class="back-tagline">Committed to Quality,<br>Service &amp; Integrity</p>

    <div class="back-name">
      <span class="word">Tolbek</span>
      <span class="suffix">Builders LLC</span>
    </div>

    <p class="pitch">Are you<br>thinking about a new<br>building on your property,<br>or renovating an existing structure?</p>
  </section>
</body>
</html>
```